KTWG application splash screen

We need a 1024x768 image for use as an application splash screen.
The image will be displayed full screen on an 10 inch industrial PC 1024x768 screen while our application is launching. The image should convey that the application is "Waiting for connection to Wi-Fi access point..." and include a graphic of the industrial PC connected to the access point via an Ethernet cable. A list of troubleshooting steps should be included at the bottom of the image. The troubleshooting steps should not be the main focus of the image and should be shown in a smaller font (but still readable at 1024x768 displayed on a 10 inch screen).
I will include a mock up of the general idea of what we are looking for as well as image files for the industrial PC, a screenshot of our application to show on the PC's screen and the AP.
For general look and feel and a sense of corporate branding please review our website https://marrowgatesoilworks.example/. The splash screen should reflect corporate branding.
Target Market(s)
Users of our application
Industry/Entity Type
Agriculture
Look and feel

```html
<!DOCTYPE html>
<html lang="en">
<head>
<meta charset="utf-8">
<title>KTWG – Waiting for Wi-Fi access point</title>
<link rel="stylesheet" href="https://fonts.googleapis.com/css2?family=Quicksand:wght@500;700&family=Tinos&display=swap">
<style>
  :root {
    --page: #000000;
    --field: #5cb27d;
    --field-light: #7cc597;
    --icon: #3a9d5a;
    --icon-dark: #2a7d45;
    --ink: #0b1a10;
    --white: #ffffff;
    --panel: #000000;
    --accent: #6fd08f;
    --device: #2b2b2b;
    --device-screen: #e9eeea;
    --ap-body: #eef0ef;
  }
  * { box-sizing: border-box; margin: 0; padding: 0; }
  html, body { width: 1200px; height: 1200px; overflow: hidden; background: var(--page); }
  .splash {
    position: absolute; left: 0; top: 150px; width: 1200px; height: 900px;
    background: var(--field); overflow: hidden;
    font-family: "Quicksand", sans-serif; color: var(--ink);
  }
  .network-glow {
    position: absolute; right: 0; top: 0; width: 380px; height: 110px;
    background: radial-gradient(ellipse at 80% 20%, var(--field-light), transparent 70%);
  }
  .headline {
    position: absolute; top: 52px; left: 0; width: 100%; text-align: center;
    font-size: 44px; font-weight: 700; letter-spacing: 0.2px; white-space: nowrap;
  }
  .cab-computer {
    position: absolute; left: 46px; top: 163px; width: 354px; height: 283px;
    border-radius: 16px; background: var(--device);
  }
  .cab-computer .app-screen {
    position: absolute; left: 33px; top: 27px; width: 286px; height: 210px;
    background: linear-gradient(180deg, var(--device-screen), #cfe3d5);
  }
  .wifi-icon { position: absolute; left: 489px; top: 193px; width: 291px; height: 254px; overflow: visible; }
  .access-point {
    position: absolute; left: 1031px; top: 143px; width: 43px; height: 304px;
    border-radius: 6px; background: linear-gradient(90deg, #d9dddb, var(--ap-body), #d9dddb);
  }
  .link-dot {
    position: absolute; width: 20px; height: 20px; border-radius: 50%;
    background: var(--ink); border: 3px solid var(--white);
  }
  .cable { position: absolute; left: 0; top: 0; width: 1200px; height: 900px; }
  .cable-label {
    position: absolute; left: 515px; top: 496px; width: 250px; text-align: center;
    color: var(--white); font-size: 26px; font-weight: 700; letter-spacing: 2px;
    white-space: nowrap;
  }
  .device-label {
    position: absolute; text-align: center; font-size: 28px; font-weight: 700; line-height: 33px;
  }
  .device-label.cab { left: 79px; top: 542px; width: 240px; }
  .device-label.ap { left: 877px; top: 542px; width: 340px; }
  .device-label .model { display: block; font-size: 20px; font-weight: 500; margin-top: 2px; }
  .troubleshooting {
    position: absolute; left: 31px; top: 646px; width: 1148px; height: 270px;
    background: var(--panel); border-radius: 12px 12px 0 0;
    font-family: "Tinos", serif; color: var(--white);
  }
  .troubleshooting h2 { position: absolute; left: 33px; top: 17px; font-size: 21px; font-weight: 400; }
  .steps { list-style: none; position: absolute; left: 28px; top: 60px; font-size: 18px; color: var(--accent); }
  .steps li { position: relative; padding-left: 20px; margin-bottom: 12px; }
  .steps li::before {
    content: ""; position: absolute; left: 0; top: 6px; width: 12px; height: 12px;
    border-radius: 50%; background: var(--white);
  }
  .substeps { list-style: none; position: absolute; top: 146px; left: 0; width: 100%; }
  .substeps li {
    position: absolute; top: 0; padding-left: 19px;
    font-size: 16px; line-height: 20.5px; color: var(--white);
  }
  .substeps li::before {
    content: ""; position: absolute; left: 0; top: 5px; width: 11px; height: 11px;
    border-radius: 50%; border: 1.5px solid var(--accent);
  }
</style>
</head>
<body>
<main class="splash">
  <div class="network-glow"></div>
  <h1 class="headline">Waiting for Connection to Wi-Fi access point...</h1>

  <div class="cab-computer" role="img" aria-label="Industrial tractor cab computer showing the KTWG seeding application">
    <div class="app-screen"></div>
  </div>

  <svg class="wifi-icon" viewBox="0 0 291 254" aria-label="Wi-Fi disconnected icon" role="img">
    <defs>
      <linearGradient id="wifiShade" x1="0" y1="0" x2="0" y2="1">
        <stop offset="0" stop-color="#3a9d5a"/>
        <stop offset="1" stop-color="#2a7d45"/>
      </linearGradient>
    </defs>
    <g fill="none" stroke="url(#wifiShade)" stroke-linecap="round" stroke-width="20">
      <path d="M15 82 A165 165 0 0 1 276 82"/>
      <path d="M55 126 A115 115 0 0 1 236 126"/>
      <path d="M93 165 A68 68 0 0 1 198 165"/>
    </g>
    <circle cx="145" cy="216" r="34" fill="url(#wifiShade)"/>
    <line x1="235" y1="18" x2="65" y2="230" stroke="#2a7d45" stroke-width="20" stroke-linecap="round"/>
  </svg>

  <div class="access-point" role="img" aria-label="Outdoor Wi-Fi access point with two antennas"></div>

  <svg class="cable" viewBox="0 0 1200 900" aria-hidden="true">
    <g stroke="#ffffff" stroke-width="4" stroke-linecap="round" stroke-dasharray="0 10" fill="none">
      <path d="M214 457 V513 H505"/>
      <path d="M1053 457 V513 H775"/>
    </g>
  </svg>
  <span class="link-dot" style="left:204px; top:447px;"></span>
  <span class="link-dot" style="left:1043px; top:447px;"></span>
  <div class="cable-label">ETHERNET CABLE</div>

  <div class="device-label cab">Tractor cab computer</div>
  <div class="device-label ap">Wi-Fi Access Point<span class="model">Fieldline AX-220 Outdoor</span></div>

  <section class="troubleshooting">
    <h2>Troubleshooting steps:</h2>
    <ul class="steps">
      <li>This screen should only be visible for a short time on boot.</li>
      <li>If this screen stays visible for more than a minute:</li>
    </ul>
    <ul class="substeps">
      <li style="left:45px; width:270px;">Verify that the Wi-Fi Access Point (AP) powers up when this system does (indicated by a green light n the side of the AP).</li>
      <li style="left:338px; width:278px;">Check the Ethernet cable between this system and the AP for damage, and replace it if necessary.</li>
      <li style="left:632px; width:228px;">Power-cycle this system and wait for it to reboot fully.</li>
      <li style="left:883px; width:215px;">If the issue persists, contact KTWG support for further assistance.</li>
    </ul>
  </section>
</main>
</body>
</html>
```